New business card/stationary for a consulting company

I am looking for a clean and very professional looking business card for my consulting company as well as corresponding stationary. I am uploading our logo. I like simple and powerful for the feel. No graphics but I am open on everything else. Below is my contact information but would like the final to be in a version I can add my employees information into and print. Thank you.

Daniel Whitcombe
dan@ferncliffadvisory.com
2870 North 9th Avenue, Summit Floor, Elm Ridge, Illinois 60531
www.ferncliffadvisory.com

Industry/Entity Type

Consulting

Contact Information for Business Card

Daniel Whitcombe
dan@ferncliffadvisory.com
www.ferncliffadvisory.com

Font styles to use
Serif
Sans Serif

Requirements
Must have
• Our logo and the business card details.
Nice to have
• our website www.ferncliffadvisory.com

```html
<!DOCTYPE html>
<html lang="en">
<head>
<meta charset="UTF-8">
<title>Ferncliff Advisory – Business Card</title>
<link href="https://fonts.googleapis.com/css2?family=Josefin+Sans:wght@400&family=Open+Sans:wght@400;700&display=swap" rel="stylesheet">
<style>
  :root {
    --navy: #0b0a63;
    --paper: #f7f7f7;
    --ink-grey: #5a5a5a;
    --backdrop: #e4e4e6;
    --white: #ffffff;
  }
  * { box-sizing: border-box; margin: 0; padding: 0; }
  html, body {
    width: 1200px; height: 904px; overflow: hidden;
    background: var(--backdrop);
  }
  .canvas {
    width: 1200px; height: 904px;
    display: flex; flex-direction: column; align-items: center; justify-content: center;
    gap: 44px;
  }
  .card {
    width: 540px; height: 308px;
    position: relative;
    box-shadow: 0 4px 14px rgba(0,0,0,0.18);
  }
  .card-back {
    background: var(--navy);
    display: flex; align-items: center; justify-content: center;
  }
  .card-back .brand {
    display: flex; align-items: center; gap: 12px;
    font-family: "Josefin Sans", sans-serif; font-weight: 400;
    font-size: 26px; letter-spacing: 2px; text-transform: uppercase;
    color: var(--white);
  }
  .brand-square {
    width: 22px; height: 22px; background: currentColor; flex: none;
  }
  .card-front {
    background: var(--paper);
    display: flex; flex-direction: column; align-items: center;
    padding-top: 44px;
  }
  .card-front .brand {
    display: flex; align-items: center; gap: 10px;
    font-family: "Josefin Sans", sans-serif; font-weight: 400;
    font-size: 22px; letter-spacing: 2px; text-transform: uppercase;
    color: var(--navy);
  }
  .holder-name {
    margin-top: 30px;
    font-family: "Open Sans", sans-serif; font-weight: 700;
    font-size: 16px; color: var(--navy);
  }
  .contact {
    position: absolute; left: 0; right: 0; bottom: 40px;
    text-align: center;
    font-family: "Open Sans", sans-serif; font-weight: 400;
    font-size: 12px; line-height: 1.6; color: var(--ink-grey);
  }
  .contact-line { display: flex; align-items: center; justify-content: center; gap: 5px; }
  .contact-line svg { width: 12px; height: 12px; flex: none; }
  .divider { margin: 0 4px; }
  .card-band {
    position: absolute; left: 0; right: 0; bottom: 0; height: 14px;
    background: var(--navy);
  }
</style>
</head>
<body>
<main class="canvas">
  <section class="card card-back" aria-label="Business card back">
    <div class="brand"><span class="brand-square"></span>Ferncliff Advisory</div>
  </section>

  <section class="card card-front" aria-label="Business card front">
    <div class="brand"><span class="brand-square"></span>Ferncliff Advisory</div>
    <p class="holder-name">Daniel Whitcombe</p>
    <div class="contact">
      <p class="contact-line">2870 North 9th Avenue, Summit Floor, Elm Ridge, Illinois 60531</p>
      <p class="contact-line">
        <svg viewBox="0 0 12 12" aria-hidden="true"><circle cx="6" cy="6" r="6" fill="#0b0a63"/><rect x="2.8" y="3.8" width="6.4" height="4.4" fill="none" stroke="#fff" stroke-width="0.9"/><path d="M2.8 3.8 L6 6.4 L9.2 3.8" fill="none" stroke="#fff" stroke-width="0.9"/></svg>
        dan@ferncliffadvisory.com
        <span class="divider">|</span>
        <svg viewBox="0 0 12 12" aria-hidden="true"><circle cx="6" cy="6" r="6" fill="#0b0a63"/><circle cx="6" cy="6" r="3.6" fill="none" stroke="#fff" stroke-width="0.8"/><ellipse cx="6" cy="6" rx="1.6" ry="3.6" fill="none" stroke="#fff" stroke-width="0.8"/><line x1="2.4" y1="6" x2="9.6" y2="6" stroke="#fff" stroke-width="0.8"/></svg>
        www.ferncliffadvisory.com
      </p>
    </div>
    <div class="card-band"></div>
  </section>
</main>
</body>
</html>
```